Redo our website for our Robotics company

We sell robotic equipment to the restaurant industry. Our current robot, is a cooking robot that cooks up to 15 lbs of food. We will provide a prior website as well as brand guidelines. We plan on using wordpress and take advantage of wordpress's visual (no code) editor.

Current website - https://kelvatrix88.com/ (please note we are only selling Tammo now and no longer selling Plavo+

We want someone to take our existing content and design the website as well as layout our content we provide. Here's a suggested site layout:

✅ KelvaTrix88 Website Wireframe / Site Map
1. Home

Purpose: Introduce Tammo, establish credibility, drive demo requests.

Sections:

Hero Section

Headline: “Meet Tammo — Your New Robotic Chef for High-Volume, Consistent Cooking.”

Sub-headline: Increase throughput. Reduce labor. Deliver perfect food every time.

CTA: Request a Demo + Watch Tammo Cook

Visual: Video loop or hero animation of Tammo in action.

How Tammo Works (3-4 steps)

Step cards: Load Ingredients → Select Recipe → Tammo Cooks → Serve

Icons and short explanations.

Key Benefits

Labor savings

Zero inconsistency

24/7 uptime

Throughput increases (30–50% faster)

Health & safety compliance

Who It’s For

QSR restaurants

Fast casual

Catering/commissaries

Ghost kitchens

Case Studies / Testimonials

Logo bar + quotes

“Tammo helped us reduce cooking times by 40%.”

Video Section

“Watch Tammo cook a full batch from start to finish.”

CTA Section

Big banner: Book a Demo

2. Product: “Meet Tammo”

Purpose: Deep dive into hardware, software, safety, reliability.

Sections:

Overview

What Tammo is

What tasks it automates

Where it fits in a kitchen

Hardware Features

High-temperature cooking chamber

Precision sensors

Automated stirring

Automated dispensing

Safety mechanisms (locking lids, auto-shutoff)

Software & AI

Recipe automation

IoT dashboard

Remote monitoring

Predictive maintenance

Specs Table

Dimensions

Power requirements

Capacity (lbs per batch)

Safety certifications

Gallery

Close-ups, installation photos, process shots

CTA: Request a Demo

3. Solutions

Purpose: Show that Tammo solves real operational problems.

Sub-pages or sections:

For Quick-Service Restaurants

Reduce labor cost

Speed up peak-hour demand

For Catering & Commissaries

Large-batch consistency

Automate repetitive cooking tasks

For High-Growth Chains

Replicable quality across multiple locations

Centralized recipe control

Each solution page includes:

A problem statement

How Tammo solves it

Metrics / KPIs

Relevant testimonial

CTA

4. ROI / Economics

Purpose: Sell the financial story clearly.

Sections:

Savings Calculator

Labor hours saved

Cost savings

Throughput increases

Food waste reduction

Before & After Comparison

Traditional kitchen vs. robotic kitchen

Sample ROI

“Payback in as little as 3–6 months.”

Download Full ROI Report (PDF)

5. Case Studies

Purpose: Social proof + real results.

Structure for each case study:

Customer background

Problem

Implementation

KPIs achieved

Labor savings

Consistency improvements

Cooking speed

Quote + photos/video

6. Pricing

Purpose: Start a commercial conversation.

Include:

Subscription model (monthly / annual)

Hardware leasing or purchase options

Installation + training

Support level

CTA to book a sales call

7. About

Purpose: Build trust.

Sections:

Mission statement

Founding team

Advisors/partners

“Why we built Tammo”

8. Resources

Purpose: SEO + education.

Subpages:

Blog (e.g., “The Future of Automated Kitchens”)

Whitepapers

Technical documentation

Product videos

9. Contact

General inquiry form

Sales contact

Support portal

Careers

```html
<!DOCTYPE html>
<html lang="en">
<head>
<meta charset="utf-8">
<title>KelvaTrix88 — Meet Tammo</title>
<link href="https://fonts.googleapis.com/css2?family=Montserrat:wght@500;600;700&family=Oswald:wght@400;500&family=Tinos:wght@400;700&family=Barlow+Semi+Condensed:wght@500&display=swap" rel="stylesheet">
<style>
:root{
  --navy:#0c3266;
  --navy-glass:rgba(22,68,128,.85);
  --orange:#f4874b;
  --orange-soft:rgba(244,135,75,.88);
  --brand-red:#e8412a;
  --ink:#111;
  --muted:#555;
  --light:#f3f3f3;
  --white:#fff;
  --dark:#121418;
}
*{margin:0;padding:0;box-sizing:border-box}
html,body{width:1200px;height:3775px;overflow:hidden}
body{position:relative;background:var(--light);font-family:"Tinos",serif;color:var(--ink)}
.abs{position:absolute}
.heading{font-family:"Montserrat",sans-serif;font-weight:600}
/* nav */
.site-nav{left:0;top:0;width:1200px;height:95px;background:var(--white)}
.brand{font-family:"Montserrat",sans-serif;font-weight:700;color:var(--brand-red);font-size:30px;letter-spacing:-.5px}
.nav-links{right:70px;top:36px;display:flex;gap:29px;font-size:16px;color:#444}
.nav-links .active{color:var(--ink);font-weight:700;border-bottom:1px solid var(--ink)}
/* hero */
.hero-media{left:0;top:95px;width:1200px;height:602px;background:linear-gradient(160deg,#7c7e81 0%,#b9bbbd 45%,#8e9093 100%)}
.hero-panel{left:78px;top:190px;width:534px;height:412px;background:var(--navy-glass);border-radius:10px;padding:44px 30px 0 30px;color:var(--white)}
.hero-kicker{font-family:"Montserrat",sans-serif;font-weight:600;color:var(--orange);font-size:28px}
.hero-title{font-family:"Montserrat",sans-serif;font-weight:600;font-size:42px;line-height:49px;margin-top:6px}
.hero-sub{font-family:"Oswald",sans-serif;font-size:16px;line-height:24px;margin-top:22px}
.btn{display:inline-block;font-size:15px;padding:0 20px;height:38px;line-height:38px;border-radius:4px}
.btn-solid{background:var(--orange);color:var(--white)}
.btn-ghost{border:1.5px solid var(--white);color:var(--white);margin-left:14px;line-height:35px}
.hero-actions{margin-top:30px}
.play{width:74px;height:74px;border-radius:50%;background:var(--white)}
/* steps */
.section-title{width:1200px;text-align:center;font-family:"Montserrat",sans-serif;font-weight:600;font-size:38px}
.step{width:226px;height:246px;border-radius:8px;background:var(--navy);color:var(--white);padding:0 16px}
.step.alt{background:var(--orange)}
.step-num{position:absolute;right:16px;top:14px;font-family:"Oswald",sans-serif;font-size:64px;color:#c7ccd3;line-height:1}
.step.alt .step-num{color:#f9c7aa}
.step svg{position:absolute;left:16px;top:62px}
.step h3{position:absolute;left:16px;top:152px;font-family:"Montserrat",sans-serif;font-weight:500;font-size:19px}
.step p{position:absolute;left:16px;top:184px;width:180px;font-size:12px;line-height:16px}
/* benefits */
.benefit{width:270px}
.benefit .ico{width:66px;height:66px;border-radius:50%;background:var(--navy);display:flex;align-items:center;justify-content:center}
.benefit h4{font-family:"Montserrat",sans-serif;font-weight:500;font-size:18px;margin-top:12px}
.benefit p{font-size:13px;color:var(--muted);margin-top:3px;padding-left:2px}
.robot-stage{left:674px;top:1201px;width:526px;height:484px;background:radial-gradient(ellipse at 50% 80%,#ffffff 0%,#e6e6e6 55%,#f3f3f3 75%)}
/* audience */
.audience{left:0;top:1776px;width:1200px;height:502px;background:linear-gradient(var(--orange-soft),var(--orange-soft)),linear-gradient(#c27a55,#e8a37a)}
.aud-item{width:340px;color:var(--white)}
.aud-item h4{font-family:"Montserrat",sans-serif;font-weight:600;font-size:19px}
.aud-item p{font-size:13px;line-height:17px;color:#fde4d3;margin-top:2px}
.aud-left{text-align:right}
.aud-icon{width:60px;height:60px;border-radius:50%;background:var(--white);display:flex;align-items:center;justify-content:center}
/* testimonials */
.testi-card{left:599px;top:2444px;width:489px;height:209px;background:var(--white);border:2px solid #e5e5e5;border-radius:10px;box-shadow:0 3px 10px rgba(0,0,0,.08)}
.quote{font-size:18px}
.arrow-btn{width:35px;height:32px;border-radius:5px;display:flex;align-items:center;justify-content:center}
/* video */
.video{left:117px;top:2816px;width:971px;height:370px;border-radius:20px;background:linear-gradient(90deg,#0b0b0b 0 13%,#5b5d60 13%,#9ea1a4 50%,#4a4c4f 87%,#0b0b0b 87%)}
.caption{font-family:"Barlow Semi Condensed",sans-serif;font-weight:500;font-size:21px}
/* footer */
.footer{left:0;top:3416px;width:1200px;height:359px;background:var(--dark)}
.cta{left:111px;top:3334px;width:977px;height:179px;background:var(--orange);border-radius:18px;color:var(--white);padding:44px 40px}
.cta h2{font-family:"Montserrat",sans-serif;font-weight:600;font-size:38px;line-height:1}
.cta p{font-family:"Montserrat",sans-serif;font-size:14.5px;line-height:24px;width:680px;margin-top:20px}
.cta .btn{position:absolute;right:42px;top:72px;height:36px;line-height:36px;background:var(--white);color:var(--orange);font-size:14px;padding:0 14px}
.foot-links{left:0;top:3670px;width:1200px;display:flex;justify-content:center;gap:28px;color:var(--white);font-family:"Montserrat",sans-serif;font-size:14.5px}
.foot-rule{left:0;top:3709px;width:1200px;height:1px;background:#3a3d44}
.copyright{left:0;top:3727px;width:1200px;text-align:center;color:#cfd2d8;font-size:12px}
</style>
</head>
<body>

<header class="abs site-nav">
  <div class="abs brand" style="left:76px;top:29px">KelvaTrix88</div>
  <nav class="abs nav-links">
    <span class="active">Home</span><span>Products</span><span>Solutions</span><span>Economics</span><span>Case Studies</span><span>Pricing</span><span>More ⌄</span>
  </nav>
</header>

<section>
  <div class="abs hero-media" role="img" aria-label="Row of Tammo cooking robots in a commercial kitchen"></div>
  <div class="abs hero-panel">
    <div class="hero-kicker">Meet Tammo</div>
    <h1 class="hero-title">Your New Robotic Chef for High-Volume, Consistent Cooking.</h1>
    <p class="hero-sub">Increase Throughput. Reduce Labor. Deliver Perfect Food<br>Every Time.</p>
    <div class="hero-actions"><span class="btn btn-solid">Request a Demo</span><span class="btn btn-ghost">Watch Tammo Cook</span></div>
  </div>
  <svg class="abs play" style="left:879px;top:360px" viewBox="0 0 74 74"><circle cx="37" cy="37" r="37" fill="#fff"/><path d="M29 23 L53 37 L29 51Z" fill="#f4874b"/></svg>
</section>

<section>
  <h2 class="abs section-title" style="top:778px">How Tammo Works</h2>
  <div class="abs step" style="left:114px;top:869px"><span class="step-num">01</span>
    <svg width="66" height="66" viewBox="0 0 66 66" fill="none" stroke="#fff" stroke-width="2.5"><path d="M6 34h54c0 14-12 24-27 24S6 48 6 34z"/><circle cx="22" cy="24" r="6"/><circle cx="40" cy="20" r="7"/><path d="M50 12l6-6"/></svg>
    <h3>Load Ingredients</h3><p>Staff drops in ingredients &amp; selects a recipe.</p></div>
  <div class="abs step alt" style="left:363px;top:869px"><span class="step-num">02</span>
    <svg width="66" height="66" viewBox="0 0 66 66" fill="none" stroke="#fff" stroke-width="2.5"><rect x="12" y="6" width="42" height="54" rx="3"/><path d="M20 44h26M20 50h20M24 32h18v-8a6 6 0 0 0-18 0z"/></svg>
    <h3>Select Recipe</h3><p>Tammo's touchscreen or cloud dashboard delivers precise automation.</p></div>
  <div class="abs step" style="left:612px;top:869px"><span class="step-num">03</span>
    <svg width="66" height="66" viewBox="0 0 66 66" fill="none" stroke="#fff" stroke-width="2.5"><rect x="6" y="10" width="26" height="46" rx="2"/><rect x="32" y="30" width="28" height="26" rx="2"/><path d="M12 20h14M38 40h10"/></svg>
    <h3>Tammo Cooks</h3><p>Automated stirring, heating, and timing for perfect consistency.</p></div>
  <div class="abs step" style="left:861px;top:869px"><span class="step-num">04</span>
    <svg width="66" height="66" viewBox="0 0 66 66" fill="none" stroke="#fff" stroke-width="2.5"><path d="M10 42a23 23 0 0 1 46 0zM4 48h58M33 14v5"/><circle cx="33" cy="11" r="3"/></svg>
    <h3>Serve</h3><p>A full batch—up to 15 lbs—ready to go.</p></div>
</section>

<section>
  <h2 class="abs heading" style="left:108px;top:1204px;font-size:38px">Key Benefits</h2>
  <div class="abs benefit" style="left:110px;top:1287px"><div class="ico"><svg width="34" height="34" viewBox="0 0 34 34" fill="#fff"><circle cx="17" cy="11" r="7"/><path d="M4 32c0-8 6-12 13-12s13 4 13 12z"/></svg></div><h4>Labor Savings</h4><p>Automate repetitive cooking tasks</p></div>
  <div class="abs benefit" style="left:401px;top:1287px"><div class="ico"><svg width="32" height="32" viewBox="0 0 32 32" fill="none" stroke="#fff" stroke-width="2.5"><rect x="6" y="4" width="20" height="26" rx="2"/><path d="M10 12l3 3 5-6M10 22h12"/></svg></div><h4>Zero Inconsistency</h4><p>AI-driven precision</p></div>
  <div class="abs benefit" style="left:110px;top:1423px"><div class="ico"><svg width="34" height="34" viewBox="0 0 34 34" fill="none" stroke="#fff" stroke-width="2.5"><path d="M6 17a11 11 0 1 0 3-7.5M6 5v6h6"/><path d="M17 11v6l4 3"/></svg></div><h4>24/7 Uptime</h4><p>Built for high-volume operations</p></div>
  <div class="abs benefit" style="left:401px;top:1423px"><div class="ico"><svg width="32" height="32" viewBox="0 0 32 32" fill="none" stroke="#fff" stroke-width="2.5"><circle cx="16" cy="18" r="11"/><path d="M16 18l5-4M13 4h6M16 4v3"/></svg></div><h4>30–50% Faster Throughput</h4><p>Sed ut perspiciatis unde omnis</p></div>
  <div class="abs benefit" style="left:110px;top:1558px"><div class="ico"><svg width="30" height="32" viewBox="0 0 30 32" fill="none" stroke="#fff" stroke-width="2.5"><path d="M15 3l11 4v9c0 7-5 12-11 14C9 28 4 23 4 16V7z"/><path d="M10 16l4 4 6-7"/></svg></div><h4>Health &amp; safety compliance</h4><p>Sed ut perspiciatis unde omnis</p></div>
  <div class="abs robot-stage" role="img" aria-label="Tammo cooking robot on a white display pedestal"></div>
</section>

<section class="abs audience">
  <h2 class="abs section-title" style="top:75px;color:#fff">Who It’s For</h2>
  <svg class="abs" style="left:465px;top:164px" width="268" height="268" viewBox="0 0 268 268"><circle cx="134" cy="134" r="131" fill="none" stroke="#fff" stroke-width="3" stroke-dasharray="14 9"/></svg>
  <div class="abs" style="left:489px;top:186px;width:220px;height:220px;border-radius:50%;background:radial-gradient(#fff,#dcdcdc)" role="img" aria-label="Tammo robots grouped together"></div>
  <div class="abs aud-item aud-left" style="left:38px;top:168px"><h4>QSR Restaurants</h4><p>Excepteur sint occaecat cupidatat non proident, sunt in culpa</p></div>
  <div class="abs aud-item aud-left" style="left:38px;top:350px"><h4>Fast Casual Brands</h4><p>Excepteur sint occaecat cupidatat non proident, sunt in culpa</p></div>
  <div class="abs aud-item" style="left:819px;top:168px"><h4>Ghost Kitchens</h4><p>Excepteur sint occaecat cupidatat non proident, sunt in culpa</p></div>
  <div class="abs aud-item" style="left:819px;top:350px"><h4>Catering &amp; Commissaries</h4><p>Excepteur sint occaecat cupidatat non proident, sunt in culpa</p></div>
  <div class="abs aud-icon" style="left:393px;top:175px"><svg width="30" height="30" viewBox="0 0 30 30" fill="#0c3266"><path d="M7 18a6 6 0 0 1 2-11 7 7 0 0 1 12 0 6 6 0 0 1 2 11v8H7z"/></svg></div>
  <div class="abs aud-icon" style="left:393px;top:353px"><svg width="30" height="30" viewBox="0 0 30 30" fill="none" stroke="#0c3266" stroke-width="2.5"><circle cx="16" cy="17" r="10"/><path d="M16 17l4-4M13 3h6"/></svg></div>
  <div class="abs aud-icon" style="left:744px;top:175px"><svg width="30" height="30" viewBox="0 0 30 30" fill="none" stroke="#0c3266" stroke-width="2.5"><rect x="4" y="14" width="22" height="12"/><path d="M15 14v12M4 20h22M8 4v6"/></svg></div>
  <div class="abs aud-icon" style="left:744px;top:353px"><svg width="30" height="30" viewBox="0 0 30 30" fill="#0c3266"><path d="M5 22a10 10 0 0 1 20 0z"/><rect x="3" y="23" width="24" height="3"/><circle cx="15" cy="9" r="2"/></svg></div>
</section>

<section>
  <div class="abs" style="left:103px;top:2359px;width:395px;height:381px;background:radial-gradient(ellipse at 50% 60%,#e9e9e9,#f3f3f3 70%)" role="img" aria-label="Two Tammo service robots side by side"></div>
  <h2 class="abs heading" style="left:599px;top:2362px;font-size:40px">Our&nbsp; Testimonials</h2>
  <div class="abs testi-card">
    <svg class="abs" style="left:18px;top:36px" width="108" height="20" viewBox="0 0 108 20"><g fill="#f5a623"><path id="s" d="M10 1l2.7 6 6.3.5-4.8 4.2 1.5 6.3L10 14.7 4.3 18l1.5-6.3L1 7.5 7.3 7z"/><use href="#s" x="21"/><use href="#s" x="42"/><use href="#s" x="63"/></g><use href="#s" x="84" fill="none" stroke="#f5a623" stroke-width="1.4"/></svg>
    <svg class="abs" style="right:10px;top:20px" width="120" height="110" viewBox="0 0 120 110" fill="#ececec"><path d="M10 100c30-10 45-35 40-70 15 5 25 20 20 45-5 20-30 30-60 25zM60 100c30-10 45-35 40-70 15 5 25 20 20 45-5 20-30 30-60 25z"/></svg>
    <p class="abs quote" style="left:18px;top:72px">“Tammo helped us reduce cooking times by 40%.”</p>
    <div class="abs" style="left:18px;top:128px;display:flex;align-items:center;gap:8px"><span style="width:14px;height:14px;background:#111;border-radius:50%"></span><span class="heading" style="font-size:18px;color:#111">Ember Table</span></div>
  </div>
  <div class="abs arrow-btn" style="left:1002px;top:2680px;background:var(--orange)"><svg width="12" height="14" viewBox="0 0 12 14"><path d="M8 2L3 7l5 5" stroke="#fff" stroke-width="2" fill="none"/></svg></div>
  <div class="abs arrow-btn" style="left:1053px;top:2680px;border:1.5px solid var(--orange)"><svg width="12" height="14" viewBox="0 0 12 14"><path d="M4 2l5 5-5 5" stroke="#f4874b" stroke-width="2" fill="none"/></svg></div>
</section>

<section>
  <div class="abs video" role="img" aria-label="Video still of Tammo stirring a batch in its cooking chamber"></div>
  <svg class="abs" style="left:566px;top:2985px" width="74" height="74" viewBox="0 0 74 74"><circle cx="37" cy="37" r="37" fill="#fff"/><path d="M29 23 L53 37 L29 51Z" fill="#f4874b"/></svg>
  <p class="abs caption" style="left:0;top:3225px;width:1200px;text-align:center">Watch Tammo Cook A Full Batch From Start To Finish.</p>
</section>

<footer>
  <div class="abs footer"></div>
  <div class="abs cta">
    <h2>How Tammo Works</h2>
    <p>Lorem ipsum dolor sit amet, consectetur adipiscing elit, sed do eiusmod tempor incididunt ut labore et dolore magna aliqua.</p>
    <span class="btn">Book a Live Demo</span>
  </div>
  <div class="abs brand" style="left:0;top:3596px;width:1200px;text-align:center;font-size:40px">KelvaTrix88</div>
  <nav class="abs foot-links"><span style="font-weight:700">Home</span><span>Products</span><span>Solutions</span><span>Economics</span><span>Case Studies</span><span>Pricing</span><span>About</span><span>Resources</span><span>Contact Us</span></nav>
  <div class="abs foot-rule"></div>
  <p class="abs copyright">Copyright © 2025 KelvaTrix88. All rights reserved.</p>
</footer>

</body>
</html>
```